DuePath.com website design

We are a collection agency that collects debt from past residents of apartments on behalf of Property Management Companies. We are want to design a 3 page website with - Home - How it Works - Schedule Demo. We'd like a sketch of a skyline showing high rise apartment buildings, houses, shops, etc. We would like for there to be some animation, possibly clouds and the sun slowly moving. Maybe kids playing ball or catch or something like that. Bird flying and landing. An electric car charging (to indicate we are modern). We are looking for a friendly community vibe. The site will also need a button "Property Managers Login". When some comes to the site we would like a pop up that says "Property Managers Click Here/Past Residents Click Here" with a different icon for each that relates to the description. I've included a link to a test site we had designed so feel free to use some of the copy from it. We just aren't happy with the design. On the Home page our tag line should be "Get more payments, faster, from past residents!" and "Digital First, NOT Digital Only". All without transaction fees, we don't get paid unless we get you paid first!
Additional selling points:

24 hour virtual agent and virtual telephone agent so we don't miss any opportunities to GET YOUR MONEY!

Old school collection strategies meet cutting edge technology to create effective work flow algorithms to put the best debt collectors on your accounts with data driven intelligence to determine the best way to get paid.

No Subscription Fees
No Payment Processing Fees
No Software Fees
No Mail, Email or TXT Fees

Inquire about our FIRST PARTY accounts receivable outsourcing. You may qualify for free post move out A/R processing and AI payment negotiator for the low hanging fruit. Don't pay full collection commission when there wasn't a full collection attempt!

For the How it Works page - See the page from our previous design. I will include the link below. Please come up with your own version of this but you can use the copy from this page.

The schedule demo page will be a form that will feed to our CRM that will include:
Name
Email
Company
Title
Phone Number
Number of Units
Tell us how we can help you: (a box for them provide details)

Also include our phone number at the bottom with something like

Here is a link to our previous design test site:
https://brookpreview.net/duepath-new/
I've attached an image of the back end so you can get an idea of the colors we need, I've also included our logo. For the most part we would like most of the site to match the blue colors from our logo, but we do need to incorporate some of the yellow in the images I've attached. Possibly make the buttons on the site the yellow color? Make the sun Match the yellow? I'll leave it up to you.

```html
<!DOCTYPE html>
<html lang="en">
<head>
<meta charset="utf-8">
<title>DuePath – Home</title>
<link href="https://fonts.googleapis.com/css2?family=Teko:wght@400;500&family=Poppins:wght@400;500;600;700&display=swap" rel="stylesheet">
<style>
:root{
  --teal:#22b5cc;
  --teal-soft:#b8e9f0;
  --teal-deep:#0f6f80;
  --navy:#10293f;
  --orange:#f9a11b;
  --ink:#2b2b2b;
  --white:#ffffff;
  --black:#000000;
  --stage:#8a8a8a;
  --dim:rgba(25,25,25,.52);
}
*{margin:0;padding:0;box-sizing:border-box}
html,body{width:881px;height:1200px;overflow:hidden}
body{background:var(--stage);font-family:'Poppins',sans-serif;color:var(--ink);position:relative}
.page{position:absolute;top:43px;width:375px;height:1114px;background:var(--white);overflow:hidden}
.page--home{left:453px}
.page--popup{left:53px}
.abs{position:absolute}
.heading{font-family:'Teko',sans-serif;font-weight:500;line-height:1}

/* header */
.brand{left:34px;top:14px;display:flex;align-items:center;gap:3px;font-weight:600;font-size:10px;color:var(--teal-deep)}
.brand-mark{width:10px;height:10px;background:var(--teal);border-radius:2px}
.nav-link{top:17px;font-size:5.2px;color:var(--ink)}
.btn{display:flex;align-items:center;justify-content:center;font-weight:700;color:var(--white);border-radius:0 6px 0 6px;font-size:5px;white-space:nowrap}
.btn--teal{background:var(--teal)}
.btn--orange{background:var(--orange)}
.nav-demo{left:215px;top:15px;width:49px;height:12px}
.nav-login{left:268px;top:15px;width:72px;height:12px}

/* hero */
.hero-art{left:175px;top:32px;width:200px;height:181px;background:linear-gradient(160deg,#e6f7fa 0%,#7fd6e4 45%,#1c8fa3 80%,#0d4f5e 100%);clip-path:polygon(40% 0,100% 0,100% 100%,0 100%,0 72%,18% 45%,25% 20%)}
.hero-title{left:34px;top:72px;font-size:15.5px;color:var(--navy);white-space:nowrap}
.hero-title .accent{color:var(--teal)}
.hero-title span.line{display:block;height:17px}
.hero-copy{left:34px;top:106px;width:124px;font-size:5.3px;line-height:7.4px;text-align:justify}
.hero-btn{left:30px;top:130px;width:52px;height:12px}

/* band */
.band{left:0;top:213px;width:375px;height:41px;background:var(--teal);color:var(--white);text-align:center;font-weight:600;font-size:7.3px;line-height:12px;padding-top:9px}
.band em{font-style:normal;color:var(--orange)}

/* section headings */
.sec-title{left:0;width:375px;text-align:center;font-size:12.5px;color:var(--teal-deep)}
.sec-rule{left:180px;width:15px;height:1px;background:var(--teal)}
.sec-copy{left:38px;width:299px;text-align:center;font-size:4.9px;line-height:8px}

/* benefits */
.benefit{top:337px;width:80px;text-align:center}
.benefit-icon{width:22px;height:22px;margin:0 auto;background:#e3f5f8;border-radius:40% 50% 45% 50%;display:flex;align-items:center;justify-content:center}
.benefit-label{margin-top:7px;font-family:'Teko',sans-serif;font-size:6.3px;color:var(--teal-deep);white-space:nowrap}

/* about */
.about{left:0;top:398px;width:375px;height:146px;background:var(--teal)}
.about-name{left:48px;top:50px;width:104px;text-align:center;font-weight:700;font-size:22px;color:var(--white)}
.about-title{left:187px;top:29px;font-size:12px;color:var(--white)}
.about-rule{left:187px;top:42px;width:12px;height:1px;background:var(--white)}
.about-copy{left:187px;top:50px;width:153px;font-size:4.6px;line-height:7.2px;color:var(--white);text-align:justify}
.about-copy p+p{margin-top:2px}

/* services */
.svc-title{font-size:12.5px;color:var(--teal)}
.svc-copy{font-size:5.4px;line-height:8.7px;width:140px}
.art-1{left:222px;top:632px;width:93px;height:88px;border-radius:50%;background:radial-gradient(circle at 45% 40%,#a9ecf5 0%,#3fc3d6 55%,#e9f8fb 72%,transparent 73%)}
.art-2{left:34px;top:746px;width:119px;height:81px;border-radius:40% 45% 10% 30%;background:linear-gradient(150deg,#9fe3ee 0%,#25b1c7 55%,#117b8e 100%)}
.art-3{left:200px;top:843px;width:120px;height:98px;border-radius:45% 50% 20% 30%;background:linear-gradient(160deg,#bff0f6 0%,#44c4d7 50%,#1b93a6 100%)}

/* footer */
.footer{left:0;top:970px;width:375px;height:144px;background:var(--black);color:var(--white)}
.news-title{left:34px;top:20px;font-size:11px;color:var(--teal)}
.news-input{left:166px;top:18px;width:112px;height:13px;background:var(--white);border-radius:7px;font-size:3.6px;color:#666;padding-left:6px;display:flex;align-items:center}
.news-btn{left:281px;top:18px;width:60px;height:13px;background:var(--orange);border-radius:7px;font-size:4.4px;font-weight:700;display:flex;align-items:center;justify-content:center}
.foot-rule{left:34px;top:44px;width:307px;height:1px;background:#222}
.foot-brand{left:26px;top:60px;display:flex;align-items:center;gap:5px;font-weight:700;font-size:17px;color:var(--white)}
.foot-brand-mark{width:16px;height:16px;border:2px solid var(--white);border-radius:3px}
.foot-col{top:57px;font-size:4.8px;line-height:10px}
.foot-col h4{font-family:'Teko',sans-serif;font-weight:500;font-size:6.4px;line-height:10px;margin-bottom:3px}
.social{top:68px;width:8px;height:8px;border-radius:50%;background:var(--teal)}
.copyright{left:0;top:126px;width:375px;text-align:center;font-size:3.8px}

/* popup page */
.veil{left:0;top:0;width:375px;height:1114px;background:var(--dim)}
.modal{left:69px;top:30px;width:238px;height:147px;background:var(--white);border:1.5px solid var(--teal);border-radius:6px;overflow:hidden}
.modal-brand{left:0;top:17px;width:238px;display:flex;justify-content:center;align-items:center;gap:4px;font-weight:600;font-size:15px;color:var(--navy)}
.modal-brand-mark{width:14px;height:14px;background:var(--teal);border-radius:3px}
.modal-tag{left:0;top:39px;width:238px;text-align:center;font-size:2.8px;letter-spacing:.8px;color:var(--navy)}
.modal-copy{left:20px;top:51px;width:198px;text-align:center;font-size:4.8px;line-height:7.5px}
.modal-skyline{left:0;top:100px;width:238px;height:47px;background:linear-gradient(180deg,rgba(255,255,255,0) 0%,#d6eef3 60%,#c4e6ee 100%)}
.choice{top:72px;width:52px;height:60px;border-radius:6px;display:flex;flex-direction:column;align-items:center;padding-top:8px}
.choice--managers{left:61px;background:var(--teal);color:var(--white);box-shadow:0 2px 4px rgba(0,0,0,.2)}
.choice--residents{left:123px;background:var(--teal-soft);color:var(--navy)}
.choice-icon{width:20px;height:20px;border-radius:50%;background:rgba(255,255,255,.85)}
.choice--managers .choice-icon{background:#e7f7fa}
.choice-label{margin-top:5px;font-family:'Teko',sans-serif;font-weight:500;font-size:7.6px;line-height:8px;text-align:center}
</style>
</head>
<body>

<!-- Home page with welcome choice open -->
<div class="page page--popup">
  <div class="abs hero-art" role="img" aria-label="Isometric city with apartment towers, houses, cars, clouds and sun"></div>
  <div class="abs brand"><span class="brand-mark"></span>DuePath</div>
  <span class="abs nav-link" style="left:143px">Home</span>
  <span class="abs nav-link" style="left:173px">How it Work</span>
  <span class="abs btn btn--teal nav-demo">Schedule Demo</span>
  <span class="abs btn btn--orange nav-login">Property Managers Login</span>

  <h1 class="abs heading hero-title"><span class="line">GET MORE PAYMENTS, <span class="accent">FASTER,</span></span><span class="line accent">FROM PAST RESIDENTS!</span></h1>
  <p class="abs hero-copy">Lorem ipsum dolor sit amet, consectetur adipiscing elit, sed do eiusmod tempor et dolore magna aliqua</p>
  <span class="abs btn btn--orange hero-btn">Schedule Now</span>

  <div class="abs band">24 hour virtual agent and virtual telephone agent so we don't miss any<br>opportunities to <em>GET YOUR MONEY!</em></div>

  <h2 class="abs heading sec-title" style="top:282px">BENEFITS</h2>
  <div class="abs sec-rule" style="top:293px"></div>
  <p class="abs sec-copy" style="top:299px">Old school collection strategies meet cutting edge technology to create effective work flow algorithms to put the best debt collectors on your accounts with data driven intelligence to determine the best way to get paid.</p>
  <div class="abs benefit" style="left:15px"><div class="benefit-icon"><svg width="14" height="14" viewBox="0 0 14 14" fill="none" stroke="#222" stroke-width=".8"><rect x="2" y="1" width="10" height="9"/><path d="M4 4h6M4 6h6M4 8h4"/></svg></div><div class="benefit-label">No Subscription Fees</div></div>
  <div class="abs benefit" style="left:102px"><div class="benefit-icon"><svg width="14" height="14" viewBox="0 0 14 14" fill="none" stroke="#222" stroke-width=".8"><rect x="1" y="3" width="12" height="8" rx="1"/><path d="M1 6h12"/></svg></div><div class="benefit-label">No Payment Processing Fees</div></div>
  <div class="abs benefit" style="left:188px"><div class="benefit-icon"><svg width="14" height="14" viewBox="0 0 14 14" fill="none" stroke="#222" stroke-width=".8"><circle cx="7" cy="7" r="5"/><path d="M5 5.5 3.5 7 5 8.5M9 5.5 10.5 7 9 8.5"/></svg></div><div class="benefit-label">No Software Fees</div></div>
  <div class="abs benefit" style="left:274px"><div class="benefit-icon"><svg width="14" height="14" viewBox="0 0 14 14" fill="none" stroke="#222" stroke-width=".8"><rect x="1.5" y="3.5" width="11" height="7"/><path d="m1.5 3.5 5.5 4 5.5-4"/></svg></div><div class="benefit-label">No Mail, Email or TXT Fees</div></div>

  <section class="abs about">
    <div class="abs about-name">DuePath</div>
    <h2 class="abs heading about-title">ABOUT DUEPATH</h2>
    <div class="abs about-rule"></div>
    <div class="abs about-copy"><p>Lorem ipsum dolor sit amet, consectetur adipiscing elit, sed do eiusmod tempor incididunt ut labore et dolore magna aliqua. Ut enim ad minim veniam, quis nostrud exercitation ullamco laboris nisi ut aliquip ex ea commodo consequat. Duis aute irure dolor in reprehenderit in voluptate velit esse cillum dolore eu fugiat nulla pariatur.</p><p>Lorem ipsum dolor sit amet, consectetur adipiscing elit, sed do eiusmod tempor incididunt ut labore et dolore magna aliqua. Ut enim ad minim veniam,</p></div>
  </section>

  <h2 class="abs heading sec-title" style="top:572px">OUR SERVICES</h2>
  <div class="abs sec-rule" style="top:583px"></div>
  <p class="abs sec-copy" style="top:589px">We ensure that you maintain your valued image by using an ethical and respectful, while the aggressive, approach to your debt recovery services.</p>

  <h3 class="abs heading svc-title" style="left:33px;top:653px">Property Management<br>Debt Experts</h3>
  <p class="abs svc-copy" style="left:33px;top:684px">DuePath exclusively serves the apartment and student housing industries.</p>
  <div class="abs art-1" role="img" aria-label="Illustration of a caped property manager and a resident beside an apartment building"></div>

  <div class="abs art-2" role="img" aria-label="Illustration of two phones exchanging a dollar coin"></div>
  <h3 class="abs heading svc-title" style="left:212px;top:778px">We Make It Easy To Pay</h3>
  <p class="abs svc-copy" style="left:212px;top:795px">Our technology gives past residents multiple payment platforms.</p>

  <h3 class="abs heading svc-title" style="left:33px;top:875px">Break The Cycle</h3>
  <p class="abs svc-copy" style="left:33px;top:894px">Stop using old-school collection agencies that put you at financial and reputational risk.</p>
  <div class="abs art-3" role="img" aria-label="Illustration of people around a large megaphone"></div>

  <footer class="abs footer">
    <h3 class="abs heading news-title">Subscribe to our Newsletter</h3>
    <div class="abs news-input">Email Address</div>
    <div class="abs news-btn">SUBSCRIBE</div>
    <div class="abs foot-rule"></div>
    <div class="abs foot-brand"><span class="foot-brand-mark"></span>DuePath</div>
    <div class="abs foot-col" style="left:159px"><h4>Quick links</h4>Home<br>How it Works</div>
    <div class="abs foot-col" style="left:224px"><h4>Help links</h4>Terms&amp;condtions<br>Privacy Policy<br>Support</div>
    <div class="abs foot-col" style="left:291px"><h4>Follow Us</h4></div>
    <span class="abs social" style="left:292px"></span><span class="abs social" style="left:306px"></span><span class="abs social" style="left:319px"></span><span class="abs social" style="left:333px"></span>
    <p class="abs copyright">© 2022 DuePath | All Rights Reserved</p>
  </footer>

  <div class="abs veil"></div>

  <div class="abs modal" role="dialog" aria-label="Choose who you are">
    <div class="abs modal-skyline" role="img" aria-label="Faint city skyline"></div>
    <div class="abs modal-brand"><span class="modal-brand-mark"></span>DuePath</div>
    <p class="abs modal-tag">DEBT RECOVERY MANAGEMENT</p>
    <p class="abs modal-copy">Lorem ipsum dolor sit amet, consectetur adipiscing elit, sed do eiusmod tempor incididunt ut labore et dolore aliqua.</p>
    <div class="abs choice choice--managers"><span class="choice-icon" role="img" aria-label="Property manager icon"></span><span class="choice-label">Property<br>Managers</span></div>
    <div class="abs choice choice--residents"><span class="choice-icon" role="img" aria-label="Past resident icon"></span><span class="choice-label">Past<br>Residents</span></div>
  </div>
</div>

<!-- Home page -->
<div class="page page--home">
  <div class="abs hero-art" role="img" aria-label="Isometric city with apartment towers, houses, cars, clouds and sun"></div>
  <div class="abs brand"><span class="brand-mark"></span>DuePath</div>
  <span class="abs nav-link" style="left:143px">Home</span>
  <span class="abs nav-link" style="left:173px">How it Work</span>
  <span class="abs btn btn--teal nav-demo">Schedule Demo</span>
  <span class="abs btn btn--orange nav-login">Property Managers Login</span>

  <h1 class="abs heading hero-title"><span class="line">GET MORE PAYMENTS, <span class="accent">FASTER,</span></span><span class="line accent">FROM PAST RESIDENTS!</span></h1>
  <p class="abs hero-copy">Lorem ipsum dolor sit amet, consectetur adipiscing elit, sed do eiusmod tempor et dolore magna aliqua</p>
  <span class="abs btn btn--orange hero-btn">Schedule Now</span>

  <div class="abs band">24 hour virtual agent and virtual telephone agent so we don't miss any<br>opportunities to <em>GET YOUR MONEY!</em></div>

  <h2 class="abs heading sec-title" style="top:282px">BENEFITS</h2>
  <div class="abs sec-rule" style="top:293px"></div>
  <p class="abs sec-copy" style="top:299px">Old school collection strategies meet cutting edge technology to create effective work flow algorithms to put the best debt collectors on your accounts with data driven intelligence to determine the best way to get paid.</p>
  <div class="abs benefit" style="left:15px"><div class="benefit-icon"><svg width="14" height="14" viewBox="0 0 14 14" fill="none" stroke="#222" stroke-width=".8"><rect x="2" y="1" width="10" height="9"/><path d="M4 4h6M4 6h6M4 8h4"/></svg></div><div class="benefit-label">No Subscription Fees</div></div>
  <div class="abs benefit" style="left:102px"><div class="benefit-icon"><svg width="14" height="14" viewBox="0 0 14 14" fill="none" stroke="#222" stroke-width=".8"><rect x="1" y="3" width="12" height="8" rx="1"/><path d="M1 6h12"/></svg></div><div class="benefit-label">No Payment Processing Fees</div></div>
  <div class="abs benefit" style="left:188px"><div class="benefit-icon"><svg width="14" height="14" viewBox="0 0 14 14" fill="none" stroke="#222" stroke-width=".8"><circle cx="7" cy="7" r="5"/><path d="M5 5.5 3.5 7 5 8.5M9 5.5 10.5 7 9 8.5"/></svg></div><div class="benefit-label">No Software Fees</div></div>
  <div class="abs benefit" style="left:274px"><div class="benefit-icon"><svg width="14" height="14" viewBox="0 0 14 14" fill="none" stroke="#222" stroke-width=".8"><rect x="1.5" y="3.5" width="11" height="7"/><path d="m1.5 3.5 5.5 4 5.5-4"/></svg></div><div class="benefit-label">No Mail, Email or TXT Fees</div></div>

  <section class="abs about">
    <div class="abs about-name">DuePath</div>
    <h2 class="abs heading about-title">ABOUT DUEPATH</h2>
    <div class="abs about-rule"></div>
    <div class="abs about-copy"><p>Lorem ipsum dolor sit amet, consectetur adipiscing elit, sed do eiusmod tempor incididunt ut labore et dolore magna aliqua. Ut enim ad minim veniam, quis nostrud exercitation ullamco laboris nisi ut aliquip ex ea commodo consequat. Duis aute irure dolor in reprehenderit in voluptate velit esse cillum dolore eu fugiat nulla pariatur.</p><p>Lorem ipsum dolor sit amet, consectetur adipiscing elit, sed do eiusmod tempor incididunt ut labore et dolore magna aliqua. Ut enim ad minim veniam,</p></div>
  </section>

  <h2 class="abs heading sec-title" style="top:572px">OUR SERVICES</h2>
  <div class="abs sec-rule" style="top:583px"></div>
  <p class="abs sec-copy" style="top:589px">We ensure that you maintain your valued image by using an ethical and respectful, while the aggressive, approach to your debt recovery services.</p>

  <h3 class="abs heading svc-title" style="left:33px;top:653px">Property Management<br>Debt Experts</h3>
  <p class="abs svc-copy" style="left:33px;top:684px">DuePath exclusively serves the apartment and student housing industries.</p>
  <div class="abs art-1" role="img" aria-label="Illustration of a caped property manager and a resident beside an apartment building"></div>

  <div class="abs art-2" role="img" aria-label="Illustration of two phones exchanging a dollar coin"></div>
  <h3 class="abs heading svc-title" style="left:212px;top:778px">We Make It Easy To Pay</h3>
  <p class="abs svc-copy" style="left:212px;top:795px">Our technology gives past residents multiple payment platforms.</p>

  <h3 class="abs heading svc-title" style="left:33px;top:875px">Break The Cycle</h3>
  <p class="abs svc-copy" style="left:33px;top:894px">Stop using old-school collection agencies that put you at financial and reputational risk.</p>
  <div class="abs art-3" role="img" aria-label="Illustration of people around a large megaphone"></div>

  <footer class="abs footer">
    <h3 class="abs heading news-title">Subscribe to our Newsletter</h3>
    <div class="abs news-input">Email Address</div>
    <div class="abs news-btn">SUBSCRIBE</div>
    <div class="abs foot-rule"></div>
    <div class="abs foot-brand"><span class="foot-brand-mark"></span>DuePath</div>
    <div class="abs foot-col" style="left:159px"><h4>Quick links</h4>Home<br>How it Works</div>
    <div class="abs foot-col" style="left:224px"><h4>Help links</h4>Terms&amp;condtions<br>Privacy Policy<br>Support</div>
    <div class="abs foot-col" style="left:291px"><h4>Follow Us</h4></div>
    <span class="abs social" style="left:292px"></span><span class="abs social" style="left:306px"></span><span class="abs social" style="left:319px"></span><span class="abs social" style="left:333px"></span>
    <p class="abs copyright">© 2022 DuePath | All Rights Reserved</p>
  </footer>
</div>

</body>
</html>
```